Business card for my new company (Accounting firm)

I need a business card for my new business Brightwell Advisory and Ledger SA. Our services are accounting, tax, audit and financial management. Our customers are small companies, start-ups and new companies. The final design has to show financial security, trust and growth. Please find our logo attached to the business card. Text for the business card: Brightwell Advisory and Ledger SA Tomas Varenholt Director and Founder Certified Accountant Tel. 022 418 57 34 tv@clairevalconseil.ch www.clairevalconseil.ch Rue des Vergières 27 1201 Geneva
Target Market(s)
Our customers are small companies, start-ups and new companies.
Industry/Entity Type
Finance And Accounting
Contact Information for Business Card
Claireval Conseil et Comptes SA
Tomas Varenholt
Directeur et Fondateur
Expert-comptable diplômé
Tél. 022 418 57 34
tv@clairevalconseil.ch
www.clairevalconseil.ch
Rue des Vergières 27
1201 Genève

```html
<!DOCTYPE html>
<html lang="fr">
<head>
<meta charset="utf-8">
<title>Claireval Conseil et Comptes SA – Carte de visite</title>
<link href="https://fonts.googleapis.com/css2?family=Montserrat:wght@400;500;600&display=swap" rel="stylesheet">
<style>
  :root {
    --backdrop: #c9cacc;
    --backdrop-light: #dedfe1;
    --card-white: #ffffff;
    --brand-blue: #29a8e0;
    --brand-blue-deep: #1f8fcb;
    --ink-dark: #2b2f33;
    --ink-grey: #6d7277;
    --rule-grey: #c4c7ca;
  }
  * { margin: 0; padding: 0; box-sizing: border-box; }
  html, body {
    width: 1200px; height: 801px; overflow: hidden;
    font-family: "Montserrat", Arial, sans-serif;
  }
  .stage {
    position: relative; width: 1200px; height: 801px;
    background: radial-gradient(ellipse at 40% 30%, var(--backdrop-light), var(--backdrop));
  }
  .card {
    position: absolute; top: 248px; width: 520px; height: 306px;
    box-shadow: 0 6px 18px rgba(0,0,0,.18);
  }
  .card--front { left: 50px; background: var(--card-white); }
  .card--back { left: 630px; background: var(--brand-blue); overflow: hidden; }

  .brand {
    position: absolute; left: 34px; top: 118px; width: 150px;
    display: flex; align-items: center; gap: 10px;
  }
  .brand__square { flex: none; width: 18px; height: 18px; background: var(--brand-blue-deep); }
  .brand__name {
    font-size: 14px; font-weight: 600; line-height: 1.25; color: var(--ink-dark);
  }
  .divider {
    position: absolute; left: 196px; top: 62px; width: 1px; height: 150px;
    background: linear-gradient(var(--rule-grey), rgba(196,199,202,0));
  }
  .identity { position: absolute; left: 222px; top: 58px; }
  .identity__name { font-size: 25px; font-weight: 500; color: var(--brand-blue); }
  .identity__role { font-size: 14px; font-weight: 600; color: var(--ink-dark); line-height: 1.35; }
  .contacts { list-style: none; margin-top: 22px; }
  .contacts__item {
    display: flex; align-items: center; gap: 8px;
    font-size: 13.5px; color: var(--ink-grey); line-height: 1.55;
  }
  .contacts__icon { width: 11px; height: 11px; fill: var(--brand-blue-deep); flex: none; }
  .address {
    position: absolute; left: 34px; bottom: 26px;
    display: flex; align-items: center; gap: 8px;
    font-size: 14px; color: var(--ink-grey);
  }
  .address .contacts__icon { width: 12px; height: 14px; }

  .pattern {
    position: absolute; inset: 0;
    background: linear-gradient(135deg, #39b3ea, var(--brand-blue) 55%, #2196d4);
  }
  .back-brand {
    position: absolute; right: 30px; bottom: 30px;
    display: flex; align-items: center; gap: 8px;
    font-size: 14px; font-weight: 600; color: var(--card-white);
  }
  .back-brand__square { width: 14px; height: 14px; background: var(--card-white); }
</style>
</head>
<body>
<main class="stage">
  <section class="card card--front" aria-label="Recto de la carte">
    <div class="brand">
      <span class="brand__square"></span>
      <span class="brand__name">Claireval Conseil et Comptes SA</span>
    </div>
    <div class="divider"></div>
    <div class="identity">
      <h1 class="identity__name">Tomas Varenholt</h1>
      <p class="identity__role">Directeur et Fondateur</p>
      <p class="identity__role">Expert-comptable diplômé</p>
      <ul class="contacts">
        <li class="contacts__item">
          <svg class="contacts__icon" viewBox="0 0 12 12"><path d="M2.5 0.5l2 2.2-1 1.3c.7 1.5 1.9 2.7 3.5 3.5l1.3-1 2.2 2-1.2 2C5 10.2 1.8 7 0.5 1.7z"/></svg>
          022 418 57 34
        </li>
        <li class="contacts__item">
          <svg class="contacts__icon" viewBox="0 0 12 12"><path d="M0 2h12v8H0z M0.8 2.6L6 6.6l5.2-4" fill="none" stroke="#1f8fcb" stroke-width="1.4"/></svg>
          tv@clairevalconseil.ch
        </li>
        <li class="contacts__item">
          <svg class="contacts__icon" viewBox="0 0 12 12"><circle cx="6" cy="6" r="5.5"/><path d="M0.5 6h11M6 0.5c-2.5 3-2.5 8 0 11M6 0.5c2.5 3 2.5 8 0 11" stroke="#fff" stroke-width=".8" fill="none"/></svg>
          www.clairevalconseil.ch
        </li>
      </ul>
    </div>
    <p class="address">
      <svg class="contacts__icon" viewBox="0 0 12 14"><path d="M6 0a5 5 0 0 1 5 5c0 3.6-5 9-5 9S1 8.6 1 5a5 5 0 0 1 5-5z"/><circle cx="6" cy="5" r="2" fill="#fff"/></svg>
      Rue des Vergières 27, 1201 Genève
    </p>
  </section>

  <section class="card card--back" aria-label="Verso de la carte">
    <div class="pattern" role="img" aria-label="Motif répétitif ton sur ton bleu"></div>
    <div class="back-brand">
      <span class="back-brand__square"></span>
      <span>Claireval</span>
    </div>
  </section>
</main>
</body>
</html>
```